Executive recruiting firm in need of business card design

Executive recruiting firm looking for a sleek, classy and modern business card design; card itself will be square shape, rounded edges and soft touch paper, our colors are dark blues in the navy color scale, silvers and grays. Reference our website for a better idea of our company's feel and goals at Tarvex-Up.com - our company message is "Employee Engagement Begins at Recruitment" this should be on the card

```html
<!DOCTYPE html>
<html lang="en">
<head>
<meta charset="utf-8">
<title>Tarvex Up – Business Card</title>
<link href="https://fonts.googleapis.com/css2?family=Open+Sans:wght@400;700&display=swap" rel="stylesheet">
<style>
  :root {
    --navy: #1b1d68;
    --navy-deep: #0c0e3c;
    --ink: #2a2d5e;
    --rule: #c4c5c9;
    --gray: #6d6f75;
    --gray-dark: #55575c;
    --paper: #f7f7f7;
    --backdrop: #3a3b3e;
    --white: #ffffff;
  }
  * { margin: 0; padding: 0; box-sizing: border-box; }
  html, body { width: 1200px; height: 840px; overflow: hidden; }
  body {
    background: var(--backdrop);
    font-family: "Open Sans", Arial, sans-serif;
    position: relative;
  }
  .card {
    position: absolute;
    top: 266px;
    width: 540px;
    height: 308px;
    border-radius: 6px;
    overflow: hidden;
    box-shadow: 0 10px 30px rgba(0,0,0,.35);
  }
  .card--front {
    left: 40px;
    background: linear-gradient(135deg, var(--navy) 0%, var(--navy-deep) 100%);
    color: var(--white);
  }
  .card--back {
    left: 620px;
    background: var(--paper);
    color: var(--gray);
  }

  .company-name {
    position: absolute;
    font-family: "Open Sans", Arial, sans-serif;
    font-weight: 400;
    line-height: 1;
    white-space: nowrap;
  }

  /* front */
  .card--front .company-name {
    left: 0; right: 0; top: 112px;
    text-align: center;
    font-size: 40px;
    color: var(--white);
  }
  .tagline {
    position: absolute;
    left: 0; right: 0; bottom: 46px;
    text-align: center;
    font-size: 14px;
    color: var(--white);
  }

  /* back */
  .card--back .company-name {
    right: 36px; top: 44px;
    font-size: 30px;
    color: var(--ink);
  }

  .rule { position: absolute; height: 1px; background: var(--rule); }
  .rule--top { left: 210px; right: 36px; top: 98px; }
  .rule--mid { left: 36px; right: 210px; top: 186px; }

  .address {
    position: absolute;
    right: 36px; top: 112px;
    text-align: right;
    font-size: 12.5px;
    font-style: normal;
    line-height: 1.5;
  }
  .person {
    position: absolute;
    left: 36px; top: 196px;
  }
  .person__name { font-weight: 700; font-size: 13px; color: var(--ink); letter-spacing: .5px; }
  .person__title { font-size: 12px; color: var(--gray); }
  .contacts {
    position: absolute;
    left: 36px; top: 232px;
    list-style: none;
    font-size: 11.5px;
    line-height: 15px;
  }
  .contacts li { display: flex; align-items: center; gap: 8px; }
  .contacts svg { width: 10px; height: 10px; fill: var(--ink); flex: none; }

  .edge-band {
    position: absolute; left: 0; right: 0; bottom: 0; height: 9px;
  }
</style>
</head>
<body>

<section class="card card--front" aria-label="Card front">
  <p class="company-name">Tarvex Up</p>
  <p class="tagline">Employee Engagement Begins at Recruitment</p>
</section>

<section class="card card--back" aria-label="Card back">
  <p class="company-name">Tarvex Up</p>
  <div class="rule rule--top"></div>

  <address class="address">
    240 West Linden Ave<br>
    Marlow Springs, CA<br>
    www.tarvex-up.com
  </address>

  <div class="rule rule--mid"></div>

  <div class="person">
    <p class="person__name">DANIEL REYES</p>
    <p class="person__title">CEO/FOUNDER</p>
  </div>

  <ul class="contacts">
    <li><svg viewBox="0 0 10 10"><path d="M2 0.5 L3.6 2.8 L2.7 3.8 Q3.8 6 6.2 7.3 L7.2 6.4 L9.5 8 L8.4 9.5 Q3.6 9 0.5 1.6 Z"/></svg>555 214 3086</li>
    <li><svg viewBox="0 0 10 10"><path d="M2.5 0 H7.5 V10 H2.5 Z M3.3 1 V8 H6.7 V1 Z"/></svg>555 730 4172</li>
    <li><svg viewBox="0 0 10 10"><path d="M2.5 0 H7.5 V3 H9.5 V8 H0.5 V3 H2.5 Z M3.2 0.8 V3 H6.8 V0.8 Z M2 5 H8 V6 H2 Z M2.5 8.5 H7.5 V10 H2.5 Z"/></svg>555 908 6251</li>
    <li><svg viewBox="0 0 10 10"><path d="M0 1.5 H10 V8.5 H0 Z M0.8 2.3 L5 5.5 L9.2 2.3 Z"/></svg>daniel@tarvex-up.com</li>
  </ul>

  <svg class="edge-band" viewBox="0 0 540 9" preserveAspectRatio="none" aria-hidden="true">
    <polygon points="0,0 296,0 288,9 0,9" fill="var(--navy)"/>
    <polygon points="300,0 540,0 540,9 292,9" fill="var(--gray-dark)"/>
  </svg>
</section>

</body>
</html>
```